Digital Transformation Company Trade Show Banners

I am looking for help designing banners for an upcoming trade show. One would be for our company and one would be for our product. I am planning on purchasing retractable banners with a size of 33" x 81". Details are attached.

```html
<!DOCTYPE html>
<html lang="en">
<head>
<meta charset="utf-8">
<title>NexaShift and Kovra Trade Show Banners</title>
<link rel="stylesheet" href="https://fonts.googleapis.com/css2?family=Krona+One&family=Oswald:wght@500&family=Hind:wght@400;500;600&family=Montserrat:wght@700;800&display=swap">
<style>
:root{
  --stage:#e8e8eb;
  --navy:#13253d;
  --orange:#f2712a;
  --steel:#3c7db3;
  --charcoal:#25232b;
  --white:#ffffff;
  --ink:#1a1a1f;
  --night:#1f1a33;
  --card:#1c1829;
  --plum:#93478f;
  --violet:#8d36d8;
  --team-purple:#9a3cd6;
  --team-blue:#2b8be8;
  --team-red:#e8432e;
  --paper:#f4f4f6;
}
*{box-sizing:border-box;margin:0;padding:0}
html,body{width:1200px;height:2220px;overflow:hidden;background:var(--stage)}
.canvas{position:relative;width:1200px;height:2220px}
.banner{position:absolute;top:447px;width:540px;height:1326px;overflow:hidden;box-shadow:0 4px 14px rgba(0,0,0,.15)}
.banner *{position:absolute}
.company{left:50px;background:var(--charcoal)}
.product{left:610px;background:var(--night)}
.center{left:0;right:0;text-align:center}

/* company banner */
.company .top-panel{left:0;top:0;width:540px;height:410px;background:var(--white)}
.company .brand{left:0;right:0;top:62px;display:flex;justify-content:center;align-items:center;gap:14px}
.company .brand span{position:static;font-family:"Krona One",sans-serif;font-size:40px;color:var(--navy);letter-spacing:1px}
.company .brand i{position:static;display:block;width:22px;height:22px;background:var(--orange)}
.company .kicker{top:170px;font-family:"Krona One",sans-serif;font-size:33px;letter-spacing:9px;color:var(--ink)}
.company .headline{top:210px;font-family:"Krona One",sans-serif;font-size:45px;line-height:52px;color:var(--orange)}
.company .intro{top:325px;left:40px;right:40px;font-family:"Hind",sans-serif;font-size:17px;line-height:20px;font-weight:500;color:var(--ink);text-align:center}
.company .photo{left:0;top:410px;width:540px;height:300px;background:linear-gradient(180deg,#0d2244 0%,#12408a 35%,#0e2a55 70%,var(--charcoal) 100%)}
.company .section-title{top:688px;font-family:"Krona One",sans-serif;font-size:30px;color:var(--orange)}
.offers{left:14px;top:738px;width:512px;height:135px}
.offer{top:0;width:128px;height:135px;text-align:center}
.offer + .offer{border-left:1px solid var(--orange)}
.offer b{left:39px;top:0;width:50px;height:50px;background:var(--steel)}
.offer p{left:0;right:0;top:62px;font-family:"Hind",sans-serif;font-size:16px;line-height:18px;font-weight:600;color:var(--white)}
.offer:nth-child(1){left:0}.offer:nth-child(2){left:128px}.offer:nth-child(3){left:256px}.offer:nth-child(4){left:384px}
.company .question{left:60px;top:905px;width:420px;height:42px}
.company .question span{left:0;right:0;top:10px;text-align:center;font-family:"Krona One",sans-serif;font-size:19px;color:var(--white)}
.company .phone{top:965px;font-family:"Krona One",sans-serif;font-size:40px;color:var(--white)}
.company .web{top:1030px;font-family:"Montserrat",sans-serif;font-weight:800;font-size:21px;letter-spacing:12px;color:var(--white)}
.company .stripe-art{left:0;top:1080px;width:540px;height:246px;background:linear-gradient(135deg,var(--charcoal) 20%,#4a3a36 55%,#2f4a66 100%)}

/* product banner */
.product .lower-panel{left:0;top:691px;width:540px;height:489px;background:var(--paper)}
.product .brand{left:0;right:0;top:50px;display:flex;justify-content:center;align-items:center;gap:20px}
.product .brand span{position:static;font-family:"Krona One",sans-serif;font-size:56px;color:var(--white);letter-spacing:4px}
.product .brand i{position:static;display:block;width:60px;height:60px;border-radius:50%;background:var(--plum)}
.product .kicker{top:198px;font-family:"Krona One",sans-serif;font-size:23px;color:var(--white)}
.product .headline{top:224px;font-family:"Oswald",sans-serif;font-weight:500;font-size:48px;color:var(--white);line-height:56px}
.product .accent{top:278px;font-family:"Krona One",sans-serif;font-size:30px;color:var(--plum)}
.product .visual{left:0;top:322px;width:540px;height:198px;background:radial-gradient(ellipse at 50% 55%,#3b3f8e 0%,#2a2660 40%,var(--night) 75%)}
.product .mission{top:528px;left:50px;right:50px;text-align:center;font-family:"Montserrat",sans-serif;font-weight:700;font-size:14px;line-height:17px;color:var(--white)}
.teams{left:58px;top:627px;width:432px;height:268px}
.team{width:211px;height:128px;background:var(--card);border-radius:6px}
.team.top{top:0;border:2px solid var(--white)}
.team.bottom{top:138px}
.team.left{left:0}.team.right{left:221px}
.team svg{left:10px;top:14px}
.team h3{left:56px;top:24px;font-family:"Montserrat",sans-serif;font-size:16px;font-weight:700}
.team p{left:10px;right:10px;top:60px;font-family:"Hind",sans-serif;font-size:12.5px;line-height:15px;color:#d8d6e0}
.product .section-title{top:945px;left:50px;font-family:"Krona One",sans-serif;font-size:25px;color:var(--night)}
.service{width:230px;height:54px}
.service b{left:0;top:0;width:50px;height:50px;background:var(--violet)}
.service p{left:63px;top:2px;font-family:"Hind",sans-serif;font-size:21px;line-height:23px;font-weight:500;color:var(--ink)}
.service.one{left:54px;top:992px}.service.two{left:293px;top:992px}
.service.three{left:54px;top:1058px}.service.four{left:293px;top:1058px}
.service.single p{top:12px}
.product .contact{top:1196px;font-family:"Krona One",sans-serif;font-size:17px;letter-spacing:7px;color:var(--violet)}
.product .phone{top:1224px;font-family:"Krona One",sans-serif;font-size:32px;color:var(--white)}
.product .web{top:1280px;font-family:"Montserrat",sans-serif;font-weight:800;font-size:21px;letter-spacing:11px;color:var(--white)}
</style>
</head>
<body>
<main class="canvas">

  <section class="banner company" aria-label="NexaShift company banner">
    <div class="top-panel"></div>
    <div class="brand"><span>NEXASHIFT</span><i></i></div>
    <h2 class="kicker center">LOOKING TO</h2>
    <h1 class="headline center">THRIVE IN THE<br>DIGITAL AGE?</h1>
    <p class="intro">NexaShift is a digital transformation consulting firm dedicated to helping our clients securely and effectively reach their technology goals.</p>
    <div class="photo" role="img" aria-label="Photo of the glowing Earth at night wrapped in a blue network grid"></div>
    <h2 class="section-title center">WE PROVIDE</h2>
    <div class="offers">
      <div class="offer"><b></b><p>Digital Transformation consulting</p></div>
      <div class="offer"><b></b><p>Technology solution</p></div>
      <div class="offer"><b></b><p>Cybersecurity services</p></div>
      <div class="offer"><b></b><p>Training &amp; workshops</p></div>
    </div>
    <div class="question">
      <svg width="420" height="42" viewBox="0 0 420 42" style="left:0;top:0">
        <polygon points="6,42 22,0 28,0 12,42" fill="var(--white)"/>
        <polygon points="30,42 46,0 400,0 384,42" fill="var(--orange)"/>
        <polygon points="392,42 408,0 414,0 398,42" fill="var(--white)"/>
      </svg>
      <span>HAVE ANY QUESTIONS?</span>
    </div>
    <p class="phone center">1-800-555-0142</p>
    <p class="web center">WWW.NEXASHIFT.IO</p>
    <div class="stripe-art" role="img" aria-label="Angular orange and blue stripe decoration"></div>
  </section>

  <section class="banner product" aria-label="Kovra product banner">
    <div class="lower-panel"></div>
    <div class="brand"><i></i><span>KOVRA</span></div>
    <h2 class="kicker center">UNLOCK YOUR FULL</h2>
    <h1 class="headline center">POTENTIAL AND OVERCOME</h1>
    <h2 class="accent center">YOUR CHALLENGES!</h2>
    <div class="visual" role="img" aria-label="Illustration of two starry cosmic hands reaching toward each other"></div>
    <p class="mission">KOVRA AIMS TO BE THE GO-TO PLATFORM FOR #CYBERSECURITY TEAMS OF ALL COLORS COLLABORATE, DISCOVER AND IMPROVE HOW THEY CONDUCT CYBER OPERATIONS.</p>

    <div class="teams">
      <div class="team top left">
        <svg width="40" height="34" viewBox="0 0 40 34"><g fill="var(--team-purple)"><circle cx="9" cy="10" r="5"/><circle cx="31" cy="10" r="5"/><circle cx="20" cy="7" r="6.5"/><rect x="1" y="17" width="14" height="15" rx="4"/><rect x="25" y="17" width="14" height="15" rx="4"/><rect x="11" y="15" width="18" height="18" rx="5"/></g></svg>
        <h3 style="color:var(--team-purple)">Purple Teams</h3>
        <p>Consolidate &amp; collaborate on Red and Blue Team events in real-time.</p>
      </div>
      <div class="team top right">
        <svg width="40" height="34" viewBox="0 0 40 34"><g fill="var(--team-blue)"><circle cx="9" cy="10" r="5"/><circle cx="31" cy="10" r="5"/><circle cx="20" cy="7" r="6.5"/><rect x="1" y="17" width="14" height="15" rx="4"/><rect x="25" y="17" width="14" height="15" rx="4"/><rect x="11" y="15" width="18" height="18" rx="5"/></g></svg>
        <h3 style="color:var(--team-blue)">Blue Teams</h3>
        <p>Collaborate on &amp; track incident response actions and threat hunting operations.</p>
      </div>
      <div class="team bottom left">
        <svg width="40" height="34" viewBox="0 0 40 34"><g fill="var(--team-red)"><circle cx="9" cy="10" r="5"/><circle cx="31" cy="10" r="5"/><circle cx="20" cy="7" r="6.5"/><rect x="1" y="17" width="14" height="15" rx="4"/><rect x="25" y="17" width="14" height="15" rx="4"/><rect x="11" y="15" width="18" height="18" rx="5"/></g></svg>
        <h3 style="color:var(--team-red)">Red Teams</h3>
        <p>Collaborate on &amp; track Red Team mission planning, execution, and debriefing.</p>
      </div>
      <div class="team bottom right">
        <svg width="40" height="34" viewBox="0 0 40 34"><g fill="var(--white)"><circle cx="9" cy="10" r="5"/><circle cx="31" cy="10" r="5"/><circle cx="20" cy="7" r="6.5"/><rect x="1" y="17" width="14" height="15" rx="4"/><rect x="25" y="17" width="14" height="15" rx="4"/><rect x="11" y="15" width="18" height="18" rx="5"/></g></svg>
        <h3 style="color:var(--white)">White Teams</h3>
        <p>Oversee cyber engagements, inject white cards, complete learning objectives.</p>
      </div>
    </div>

    <h2 class="section-title">MANAGED SERVICES</h2>
    <div class="service one"><b></b><p>On-site<br>Support</p></div>
    <div class="service two single"><b></b><p>Training</p></div>
    <div class="service three"><b></b><p>Managed<br>Cyber Exercises</p></div>
    <div class="service four"><b></b><p>Custom<br>Integrations</p></div>

    <p class="contact center">CONTACT US TO LEARN MORE</p>
    <p class="phone center">1-800-555-0142</p>
    <p class="web center">WWW.KOVRA.COM</p>
  </section>

</main>
</body>
</html>
```